Buch-/eBook-Cover für Lern- und Prüfungscoaching
Zielgruppe
Lernende, Erwachsene, Eltern
Mein Unternehmen bietet Lerncoaching und Prüfungscoaching für Studenten und Schüler an.
Das Buch ist für lernende, die sich mit Ihren eigenen Lernweg beschäftigen wollen.
Aufgabenstellung
Ich benötige ein ansprechendes Buch-Cover. Das Format für das Buch ist 15,24 x 22,86 cm (6' x 9').
Mein Buch Cover soll sich aber deutlich von den anderen Büchern abheben und Erwachsene ansprechen.
Wichtig ist mir auch einen Wiedererkennungswert vom Buch-Cover zu haben.
Bitte um ein ansprechendes Bild, denn ich möchte mich deutlich von meiner Konkurrenz abheben.
Buchtitel: Forme deine Wissensreise
Untertitel: Entdecke deinen eigenen Pfad zum Verstehen!
Autorin: Helga Borwitz
Das Buch soll meinen bisherigen Büchern in der Stilrichtung entsprechen. Der Hintergrund in demselben Blau. https://www.buchkarawane.de/dp/K7TQ82WXRA
Elemente vom Cover:
aufgeschlagenes Buch (dynamisch) Weg vom Buch weg eine Person unisex (symbolisch) auf den Weg, bunte Stifte
Lernweg im Leben eines Menschen
Text für den Buchrücken:
Forme deine Wissensreise: Entdecke deinen individuellen Weg zum erfolgreichen Lernen
Du hast es in der Hand! Deine Lernbiografie ist einzigartig – genau wie du. In diesem Buch lernst du, wie du deine persönliche Lerngeschichte erkennst und sie gezielt nutzt, um deine Lernziele mit Leichtigkeit und Motivation zu erreichen. Ob Prüfungsstress, fehlende Motivation oder unklare Lernstrategien – hier findest du praktische Tipps, die genau zu dir passen.
Lerne, wie du:
• Effektive Lernstrategien entwickelst, die für dich funktionieren
• Deine Stärken und Erfahrungen einsetzt, um dein volles Potenzial zu entfalten
• Blackouts und Stress in Prüfungen überwindest
• Deine Zeit besser managst und dabei noch Zeit für Spaß hast
• Deine Lernziele klar und motivierend definierst
Dieses Buch zeigt dir Schritt für Schritt, wie du aus deinen bisherigen Lernerfahrungen lernst und sie in deine Erfolgsstrategie verwandelst. Egal, ob du gerade für die nächste Prüfung lernst oder deinen Lernweg langfristig optimieren mÃ..

```html
<!DOCTYPE html>
<html lang="de">
<head>
<meta charset="utf-8">
<title>Forme deine Wissensreise – Buchumschlag</title>
<link href="https://fonts.googleapis.com/css2?family=Noto+Serif:wght@400;500&family=Patrick+Hand+SC&family=Permanent+Marker&display=swap" rel="stylesheet">
<style>
  :root {
    --bg: #2c313c;
    --back-blue: #4ea2d6;
    --spine-blue: #3d8ecb;
    --front-top: #3580c0;
    --front-bottom: #9cc0e2;
    --lime: #c8d42a;
    --lime-pale: #eef0a8;
    --ink-violet: #3b3a9a;
    --navy: #1f2a66;
    --white: #ffffff;
    --title-red: #e0322e;
    --accent-yellow: #e7e931;
  }
  * { margin: 0; padding: 0; box-sizing: border-box; }
  html, body { width: 1200px; height: 900px; overflow: hidden; background: var(--bg); }
  .spread {
    position: absolute; left: 60px; top: 60px;
    width: 1080px; height: 780px; display: flex;
    box-shadow: 0 12px 30px rgba(0,0,0,.35);
  }
  .serif { font-family: "Noto Serif", Georgia, serif; }
  .hand { font-family: "Patrick Hand SC", "Comic Sans MS", cursive; }

  /* back cover */
  .back-cover {
    width: 515px; height: 100%; background: var(--back-blue);
    padding: 70px 48px 0; text-align: center; color: var(--ink-violet);
  }
  .back-heading { color: var(--white); font-size: 19px; line-height: 1.3; font-weight: 500; }
  .back-heading .caps { text-transform: uppercase; letter-spacing: .5px; }
  .back-intro { margin-top: 34px; font-size: 13.2px; line-height: 1.42; }
  .learn-label {
    margin: 28px auto 0; display: inline-block; color: var(--accent-yellow);
    font-size: 24px; border-bottom: 2px dotted var(--accent-yellow); padding: 0 8px 2px;
  }
  .learn-list { list-style: none; margin-top: 16px; font-size: 15.5px; line-height: 1.32; }
  .learn-list li::before { content: "• "; }
  .back-outro { margin-top: 28px; font-size: 13.2px; line-height: 1.42; }
  .back-tagline { margin-top: 46px; font-size: 25px; line-height: 1.2; }

  /* spine */
  .spine {
    width: 50px; height: 100%; background: var(--spine-blue);
    position: relative; color: var(--navy);
  }
  .spine-title, .spine-author {
    position: absolute; left: 50%; white-space: nowrap;
    transform: translateX(-50%) rotate(90deg); transform-origin: center;
  }
  .spine-title { top: 290px; font-size: 11px; }
  .spine-title .hand { font-size: 14px; }
  .spine-author { top: 700px; font-size: 11px; letter-spacing: 2px; text-transform: uppercase; }

  /* front cover */
  .front-cover {
    width: 515px; height: 100%; position: relative; overflow: hidden;
    background: linear-gradient(180deg, var(--front-top) 0%, var(--front-bottom) 60%, var(--front-bottom) 100%);
    text-align: center;
  }
  .author { position: absolute; top: 60px; width: 100%; color: var(--accent-yellow); font-size: 27px; }
  .author-rule {
    position: absolute; top: 112px; left: 70px; right: 70px;
    border-top: 2px dotted var(--accent-yellow);
  }
  .title-top {
    position: absolute; top: 138px; width: 100%; color: var(--white);
    font-size: 40px; letter-spacing: 1px; text-transform: uppercase;
  }
  .title-main {
    position: absolute; top: 190px; width: 100%; color: var(--title-red);
    font-family: "Permanent Marker", "Comic Sans MS", cursive; font-size: 52px; letter-spacing: 1px;
  }
  .lime-wave { position: absolute; left: 0; top: 300px; }
  .cover-illustration {
    position: absolute; left: 40px; top: 370px; width: 440px; height: 300px;
    border-radius: 14px;
    background: radial-gradient(ellipse at 50% 45%, #e9578c 0%, #2fa596 40%, #3f2f8f 70%, rgba(200,212,42,0) 100%);
    opacity: .85;
  }
  .subtitle-band {
    position: absolute; left: 0; right: 0; top: 712px; height: 40px;
    background: var(--lime-pale); color: var(--navy);
    font-size: 16px; line-height: 40px;
  }
</style>
</head>
<body>
<div class="spread">
  <section class="back-cover">
    <h2 class="back-heading serif"><span class="caps">Forme deine Wissensreise:</span><br>Entdecke deinen individuellen Weg zum erfolgreichen Lernen</h2>
    <p class="back-intro serif">Du hast es in der Hand! Deine Lernbiografie ist einzigartig – genau wie du. In diesem Buch lernst du, wie du deine persönliche Lerngeschichte erkennst und sie gezielt nutzt, um deine Lernziele mit Leichtigkeit und Motivation zu erreichen. Ob Prüfungsstress, fehlende Motivation oder unklare Lernstrategien – hier findest du praktische Tipps, die genau zu dir passen.</p>
    <div class="learn-label hand">Du lernst:</div>
    <ul class="learn-list hand">
      <li>Effektive Lernstrategien entwickelst, die für dich funktionieren</li>
      <li>Deine Stärken und Erfahrungen einsetzt, um dein volles Potenzial zu entfalten</li>
      <li>Blackouts und Stress in Prüfungen überwindest</li>
      <li>Deine Zeit besser managst und dabei noch Zeit für Spaß hast</li>
      <li>Deine Lernziele klar und motivierend definierst</li>
    </ul>
    <p class="back-outro serif">Dieses Buch zeigt dir Schritt für Schritt, wie du aus deinen bisherigen Lernerfahrungen lernst und sie in deine Erfolgsstrategie verwandelst. Egal, ob du gerade für die nächste Prüfung lernst oder deinen Lernweg langfristig optimieren möchtest – du kannst es schaffen! Lass dich von deiner eigenen Lernbiografie inspirieren und entdecke den Weg zu mehr Spaß, Erfolg und Selbstvertrauen beim Lernen.</p>
    <p class="back-tagline hand">Forme deine Wissensreise –<br>dein Schlüssel zum Lernerfolg!</p>
  </section>

  <section class="spine">
    <div class="spine-title"><span class="hand">Forme deine Wissensreise</span> <span class="serif">– Entdecke deinen individuellen Weg zum Erfolg!</span></div>
    <div class="spine-author serif">Helga Borwitz</div>
  </section>

  <section class="front-cover">
    <div class="author serif">Helga Borwitz</div>
    <div class="author-rule"></div>
    <div class="title-top serif">Forme deine</div>
    <div class="title-main">WISSENSREISE</div>
    <svg class="lime-wave" width="515" height="480" viewBox="0 0 515 480" aria-hidden="true">
      <path d="M515 10 C 450 -10 390 20 340 40 C 290 60 230 40 190 80 C 150 120 180 170 110 190 C 60 205 20 250 0 290 L0 480 L515 480 Z" fill="var(--lime)"/>
    </svg>
    <div class="cover-illustration" role="img" aria-label="Illustration: aufgeschlagenes Buch mit bunten Pflanzen, ein dunkler Weg führt daraus hervor, eine Person mit Gießkanne steht auf den Seiten"></div>
    <div class="subtitle-band serif">Entdecke deinen eigenen Pfad zum Verstehen!</div>
  </section>
</div>
</body>
</html>
```